Corporate website design needed

We need a Contemporary Industrial/Tech/Logistics Website design to match our logistic client's business. Our client consults and build logistics solutions that they manage but they are not a typical 3PL (3rd party logistics company) which is primarily engaged in moving boxes.
PSD file only for now, home and default templates.
COMPANY CHARACTER
DESIGN LOOK AND FEEL
• The design should also be modern and visually well organized — employing a combination of visual devices and info graphics. Keep it light and not too heavy but strong/ professional. And unique.
• The design should go beyond the typical industrial pick and pack 3PL representing [Logistics Company] as a High Tech/IT logistics company.
Some examples although these are not right for this client because they have much more content and present themselves more as a 3pl.
http://www.vobrelink-hub.example/ (More right then wrong - Like this but simplified)
http://www.durmaxfreight.example (Ugly)
http://www.tpwallerton.example (More right then wrong but different focus)
http://www.pelhamrye.example/ Too 3PL trucking… We want a bit ore high level approach
The difference, the design should be a fusion in core concepts that culminate in a design which implies the following attributes. Tech (Big data / analytics / software), Consultancy (Solutions, SME, Leader), 3PL Industry vertical solutions.
NOTE: The visualization of “tech” is not “1” and “0”, but more “software and analytics” Perhaps more like www.navimetra.example.
• They need to be seen as a solutions provider in Logistics and as in Subject matter experts
TONE
The tone needs to exude professionalism, expertise, though leadership along with technical and executional excellence.
Experienced
Knowledgeable
Confident
Determined
Straightforward
WEBSITE OBJECTIVES
• Focus C-Suite executives and logistics managers’ attention on [Logistics Company]s commanding knowledge and expertise, and unique approach to supply chain solutions producing more RFP wins
• Create an easy to scan design which decreases the reliance on text through featured text, summaries, and smaller “chunked” size bits of information.
• Convey [Logistics Company] as high-tech 3PL solutions developer and services provider with a ‘high-touch’ consultative approach.
• Showcase [Logistics Company]’s value propositions. (See Slider Content)
• Showcase [Logistics Company]’s expertise in logistical analytics.
• Gain recognition as an industry leader in evolutionary new space (supply chain 2.0)
WEBSITE STRATEGY
• Reduce reliance on text (at least within initial entry points for each section)
• Typography: Watch text line lengths and readability, bolder fonts. NO SERIFS
• Generally, create a click-through format so that users who want more details can find it, and those who don’t can get a snapshot without clicking through.
• Increase visual content through info graphics and some dynamic content, photography
• Better utilize the space on each page (e.g., add visual interest, photography and iconography where appropriate to break up copy blocks and maintain readable line lengths).
COLOR SCHEME
• Create a more engaging color scheme (the logo will remain the same under all circumstances).
• Red / grayscale may work…. Not too dark or heavy. Not too much red. Ex. quiltora.example
• Also try blues and greys. They seem to like that. Open to suggestions but don’t get to crazy. Red is in their logo but too much may be a problem.
PHOTOGRAPHY
Yes. And I will upload some.
If you pick photography please be sure to note Which stock house used and the image number!
CONTENT
The content will be presented in a more hierarchical format — with lead-ins, paragraph and section headers and navigational cues to expand lengthier content allowing the visitor to more easily scan the website. No case studies, No Social media, News while on the home page should not be over emphasized. They don't post a lot so it gets dated quickly ...
I will be uploading a wire frame and other elements.
NOTE: I uploaded my EXAMPLE mock up which is close but not close enough.
I am not a great designer. So I am looking for an alternative that exceed my design ability! These examples show the basic layout but I really want some varied alternatives.
The colors are inconsistent and type not quite right. The grey bar at top is not right and should probably go away.
Please pull the basic elements in the example together into a great design.
If you have questions please contact me.
i will upload some photography tomorrow that may be of use.
Thanks!
Updates
Hi All,
We are still evaluating the submitted designs. Sorry for the delay.
Target Market(s)
This website is primarily a validation website. Few new customers will search and find them as such...
The site should be Focused on C-Suite executives and logistics managers’ attention on [Logistics Company]s commanding knowledge and expertise, and unique approach to supply chain solutions producing more RFP wins
Industry/Entity Type
Business
Font styles to use
Requirements
Must have
- Slide show, Clearly explain who they are and what they do.
Create an easy to scan design which decreases the reliance on text through featured text, summaries, and smaller “chunked” size bits of information.
Convey [Logistics Company] as high-tech 3PL solutions developer and services
provider with a ‘high-touch’ consultative approach.
Should not have
- No Ads space
No Social media
Not too cluttered. Keep it clean.

```html
<!DOCTYPE html>
<html lang="en">
<head>
<meta charset="utf-8">
<title>Kestrel Lane Logistics</title>
<link rel="stylesheet" href="https://fonts.googleapis.com/css2?family=Open+Sans:wght@400;600;700&display=swap">
<style>
:root{
  --red:#b3121c;
  --red-dark:#8f0d15;
  --ink:#2a2a2a;
  --top:#1f1f1f;
  --footer:#2e2e2e;
  --footer-line:#444;
  --grey:#6b6b6b;
  --light:#f1f1f1;
  --hero-a:#1d4f80;
  --hero-b:#5fa1cf;
  --white:#fff;
}
*{margin:0;padding:0;box-sizing:border-box}
html,body{width:829px;height:1200px;overflow:hidden}
body{font-family:"Open Sans",Arial,sans-serif;color:var(--ink);background:var(--white);position:relative}
.topbar{height:24px;background:var(--top);color:#bbb;font-size:9px;display:flex;align-items:center;justify-content:space-between;padding:0 40px}
.topbar .links span{margin-left:18px}
.header{height:56px;display:flex;align-items:center;justify-content:space-between;padding:0 40px;border-bottom:1px solid #ddd}
.brand{display:flex;align-items:center;gap:8px;font-weight:700;font-size:15px;color:var(--ink)}
.brand .dot{width:26px;height:26px;border-radius:50%;background:var(--red)}
.nav{display:flex;gap:22px;font-size:11px;font-weight:600;color:#444;align-items:center}
.nav .search{width:14px;height:14px;border:2px solid #777;border-radius:50%}
.hero{position:relative;height:315px;background:linear-gradient(120deg,var(--hero-a),var(--hero-b) 60%,#cfe3f2)}
.hero-art{position:absolute;inset:0}
.hero-copy{position:absolute;left:58px;top:36px;width:320px;color:var(--white)}
.hero-copy h1{font-size:27px;font-weight:700;line-height:1.15}
.hero-copy h2{font-size:17px;font-weight:600;margin:4px 0 12px}
.hero-copy p{font-size:10px;line-height:1.5;opacity:.9}
.statement{height:75px;background:var(--ink);color:var(--white);font-size:14px;line-height:1.45;padding:16px 58px}
.solutions{height:180px;text-align:center;padding-top:20px}
.solutions h3{color:var(--red);font-size:20px;font-weight:600}
.solutions .lead{font-size:10px;color:var(--grey);margin:4px 0 16px}
.tiles{display:flex;justify-content:center;gap:22px}
.tile{width:118px}
.tile .box{height:64px;border:1px solid #ddd;background:var(--light);display:flex;align-items:center;justify-content:center;margin-bottom:6px}
.tile span{font-size:9.5px;color:#444;line-height:1.3;display:block}
.band{height:255px;background:var(--red);color:var(--white);display:flex;padding:20px 40px;gap:30px}
.news{width:355px}
.band h4{font-size:19px;font-weight:600;margin-bottom:10px}
.news-item{margin-bottom:12px}
.news-item b{font-size:10.5px;display:block;margin-bottom:3px}
.news-item p{font-size:8.5px;line-height:1.45;opacity:.9}
.feature{flex:1}
.feature-row{display:flex}
.feature-photo{width:210px;height:132px;background:linear-gradient(160deg,#9fb4c8,#556778)}
.feature-card{flex:1;height:132px;background:var(--ink);padding:12px;font-size:9px;line-height:1.45}
.feature-card .more{display:inline-block;margin-top:10px;background:var(--red);padding:3px 10px;font-size:9px}
.feature-meta{display:flex;gap:30px;font-size:8.5px;line-height:1.5;margin-top:8px}
.feature-meta b{font-size:10px}
.footer{height:240px;background:var(--footer);color:#ccc;display:flex;padding:24px 40px;gap:26px}
.col{width:128px}
.col h5{color:var(--white);font-size:12px;font-weight:600;margin-bottom:8px}
.col li{list-style:none;font-size:9px;line-height:1.75}
.col li::before{content:"› ";color:var(--red)}
.footer-brand{flex:1;display:flex;flex-direction:column;align-items:center;padding-top:20px}
.footer-brand .brand{color:var(--white);font-size:14px}
.sales{margin-top:22px;text-align:center;color:var(--white);font-size:11px}
.sales strong{display:block;color:#e0474f;font-size:17px;font-weight:700}
.bottombar{height:55px;background:#222;color:#999;font-size:9px;display:flex;align-items:center;justify-content:center;border-top:1px solid var(--footer-line)}
</style>
</head>
<body>
<div class="topbar"><span>☎ 800-555-0142</span><div class="links"><span>Company</span><span>Careers</span><span>Contact</span></div></div>
<header class="header">
  <div class="brand"><span class="dot"></span>Kestrel Lane Logistics</div>
  <nav class="nav"><span>Solutions ▾</span><span>Our Process ▾</span><span>Industries ▾</span><span class="search"></span></nav>
</header>
<section class="hero">
  <div class="hero-art" role="img" aria-label="Blue abstract network of connected points suggesting data and analytics"></div>
  <div class="hero-copy">
    <h1>A new way to think</h1>
    <h2>About supply chain transformation</h2>
    <p>We design, build and manage logistics solutions that turn complex supply chains into a measurable business advantage, guided by data and deep industry expertise.</p>
  </div>
</section>
<div class="statement">Kestrel Lane manages complexity, provides data-driven solutions and implements innovation and actionable strategies that delivers business results.</div>
<section class="solutions">
  <h3>Infrastructure Solutions</h3>
  <p class="lead">Our goal is to first identify who they are and what they do then how they differentiate</p>
  <div class="tiles">
    <div class="tile"><div class="box"><svg width="40" height="34"><rect x="4" y="12" width="14" height="14" fill="#c9a36b"/><rect x="20" y="12" width="14" height="14" fill="#b48a52"/><rect x="12" y="0" width="14" height="12" fill="#d8b784"/></svg></div><span>Material Management &amp; Factory Support</span></div>
    <div class="tile"><div class="box"><svg width="40" height="34"><rect x="2" y="8" width="24" height="16" fill="#3d6fa3"/><path d="M26 12h8l4 6v6H26z" fill="#2b5580"/><circle cx="10" cy="27" r="4" fill="#333"/><circle cx="31" cy="27" r="4" fill="#333"/></svg></div><span>Retail and e-Commerce Distribution</span></div>
    <div class="tile"><div class="box"><svg width="40" height="34"><rect x="4" y="4" width="32" height="20" fill="#555"/><rect x="7" y="7" width="26" height="14" fill="#7fb3dd"/><rect x="14" y="26" width="12" height="4" fill="#555"/></svg></div><span>Information Support</span></div>
    <div class="tile"><div class="box"><svg width="40" height="34"><rect x="8" y="6" width="24" height="24" rx="3" fill="#fff" stroke="#999"/><path d="M20 10v16M12 18h16" stroke="var(--red)" stroke-width="5"/></svg></div><span>Critical Logistics</span></div>
    <div class="tile"><div class="box"><svg width="40" height="34"><circle cx="20" cy="17" r="13" fill="none" stroke="#3d6fa3" stroke-width="3"/><path d="M20 8v9l6 4" stroke="#3d6fa3" stroke-width="3" fill="none"/></svg></div><span>Supply Chain Transformation Services</span></div>
  </div>
</section>
<section class="band">
  <div class="news">
    <h4>Recent News</h4>
    <div class="news-item"><b>Kestrel Lane Logistics Ranked #1 in Distribution Operations in the Memphis area</b><p>RIDGEFIELD, NC – May 18, 2014 – Kestrel Lane Logistics, Inc., headquartered in Ridgefield, North Carolina, has once again been ranked #1 in distribution operations in the Memphis area.</p></div>
    <div class="news-item"><b>Kestrel Lane Logistics Ranked #1 in Distribution Operations in the Memphis area</b><p>RIDGEFIELD, NC – May 18, 2014 – Kestrel Lane Logistics, Inc., headquartered in Ridgefield, North Carolina, has once again been ranked #1 in distribution operations in the Memphis area.</p></div>
  </div>
  <div class="feature">
    <h4>Featured Industry</h4>
    <div class="feature-row">
      <div class="feature-photo" role="img" aria-label="Photograph of a modern glass industrial building"></div>
      <div class="feature-card">Our solutions for aerospace and defense clients combine rigorous compliance with agile supply chain design that keeps critical programs moving.<br><span class="more">Read more ›</span></div>
    </div>
    <div class="feature-meta">
      <div><b>Kestrel Lane Logistics</b><br>2180 Harlow Parkway<br>Ridgefield, NC 27000<br>800-555-0142<br>info@kestrellane.example</div>
      <div><b>General Contact</b><br>› Careers<br>› Media Relations Contact</div>
    </div>
  </div>
</section>
<footer class="footer">
  <div class="col"><h5>Our Process</h5><ul><li>Concept of operations</li><li>Designing the infrastructure</li><li>Producing the value</li><li>Managing complexity</li><li>Providing new strategies</li><li>Investing in client success</li><li>Driving business results</li></ul></div>
  <div class="col"><h5>Our Solutions</h5><ul><li>Business Analytics</li><li>Integrated Solutions</li><li>Project Financing</li><li>Project Implementation</li><li>Technology</li><li>Quality</li></ul></div>
  <div class="col"><h5>Industries We Serve</h5><ul><li>Aerospace</li><li>Defense</li><li>Electronics</li><li>Industrial</li><li>Manufacturing</li><li>Media and Entertainment</li><li>Medical</li><li>Retail</li><li>Telecom &amp; Electronics</li></ul></div>
  <div class="col"><h5>Company</h5><ul><li>Culture</li><li>Community Involvement</li><li>Major News Releases</li><li>News</li><li>Careers</li><li>Contact</li></ul></div>
  <div class="footer-brand">
    <div class="brand"><span class="dot"></span>Kestrel Lane Logistics</div>
    <div class="sales">Sales Inquiries<strong>800-555-0142</strong></div>
  </div>
</footer>
<div class="bottombar">© Kestrel Lane, Inc. 2014 &nbsp;|&nbsp; Privacy Policy &nbsp;|&nbsp; Terms of Use</div>
</body>
</html>
```